Kestrel Homes Business Card Design

We need a business card for an established builder of high quality bespoke homes in Auckland and Northland. We build and renovate homes collaboratively facilitating effective communication between owners, builders, architects, suppliers and tradespeople. We have never built or renovated a home that leaks or has faults. We only use reliable materials. We have never been sued or had legal action taken against us. We are honest builders of bespoke homes not group mass produced homes. Our niche market is in character homes. We practice sustainability and have built a lot of coastal property. We have been in business for over thirty years . We would like to see natural colors of the environment sand,sea and maybe vegetation . The design should communicate quality, sustainability,fair pricing, open communication and the originality of bespoke building. And the fact that the builder is registered.

Industry/Entity Type

Business

Contact Information for Business Card

Rowan Tellick Builders
Ph. 021583917
18 Kestrel Rd Harwood Bay Auckland 0814
PO Box 927 Mangawhai 0583

```html
<!DOCTYPE html>
<html lang="en">
<head>
<meta charset="utf-8">
<title>Kestrel Homes – Business Card</title>
<link rel="stylesheet" href="https://fonts.googleapis.com/css2?family=Source+Sans+3:wght@400;600&display=swap">
<style>
  :root {
    --backdrop: #000000;
    --card: #2f3034;
    --card-edge: #35363a;
    --brand-blue: #3b77c9;
    --text-light: #f2f2f2;
    --divider: #45464b;
  }
  * { margin: 0; padding: 0; box-sizing: border-box; }
  html, body {
    width: 1200px;
    height: 900px;
    overflow: hidden;
    background: var(--backdrop);
    font-family: "Source Sans 3", "Myriad Pro", sans-serif;
  }
  .stage { position: relative; width: 1200px; height: 900px; }
  .card {
    position: absolute;
    width: 457px;
    height: 281px;
    border-radius: 14px;
    background: linear-gradient(180deg, var(--card-edge), var(--card));
  }
  .card--front { left: 137px; top: 271px; }
  .card--back { left: 626px; top: 271px; }

  .wordmark {
    position: absolute;
    color: var(--brand-blue);
    font-weight: 600;
    white-space: nowrap;
    transform: translate(-50%, -50%);
  }
  .card--front .wordmark { left: 118px; top: 150px; font-size: 27px; }
  .card--back .wordmark { left: 228px; top: 142px; font-size: 42px; }

  .divider {
    position: absolute;
    left: 235px;
    top: 87px;
    width: 1px;
    height: 130px;
    background: var(--divider);
  }
  .contact {
    position: absolute;
    left: 252px;
    top: 94px;
    color: var(--text-light);
    font-size: 13px;
    line-height: 19px;
  }
  .contact__name {
    color: var(--brand-blue);
    font-size: 16px;
    font-weight: 600;
    line-height: 22px;
    margin-bottom: 9px;
  }
  .contact__phone {
    display: flex;
    align-items: center;
    gap: 4px;
    margin-bottom: 11px;
  }
  .contact__phone svg { width: 10px; height: 10px; fill: var(--brand-blue); }
</style>
</head>
<body>
<main class="stage">
  <section class="card card--front">
    <div class="wordmark">Kestrel Homes</div>
    <div class="divider"></div>
    <div class="contact">
      <p class="contact__name">Rowan Tellick Builders</p>
      <p class="contact__phone">
        <svg viewBox="0 0 24 24" aria-hidden="true"><path d="M6.6 10.8a15.2 15.2 0 0 0 6.6 6.6l2.2-2.2a1 1 0 0 1 1-.25 11.4 11.4 0 0 0 3.6.57 1 1 0 0 1 1 1V20a1 1 0 0 1-1 1A17 17 0 0 1 3 4a1 1 0 0 1 1-1h3.5a1 1 0 0 1 1 1c0 1.25.2 2.45.57 3.57a1 1 0 0 1-.25 1z"/></svg>
        021583917
      </p>
      <p>18 Kestrel Rd Harwood Bay</p>
      <p>Auckland 0814</p>
      <p>PO Box 927 Mangawhai 0583</p>
    </div>
  </section>
  <section class="card card--back">
    <div class="wordmark">Kestrel Homes</div>
  </section>
</main>
</body>
</html>
```